italian food processing equipment manufacturer selling worldwide look for a new business card for al

Our headquarter is in Italy but we have different regional offices : Chicago, Moscow and Singapore, plus an agent in Brasil. We would like an image to exlain ONE TEAM, ONE MISSION, GLOBAL SOLUTION.

```html
<!DOCTYPE html>
<html lang="en">
<head>
<meta charset="utf-8">
<title>Corvane Business Card</title>
<link rel="stylesheet" href="https://fonts.googleapis.com/css2?family=Open+Sans:wght@400;600&family=Cormorant+Garamond:ital@1&display=swap">
<style>
  :root {
    --backdrop: #2b2724;
    --card: #141414;
    --card-edge: #1d1d1d;
    --ink-white: #f4f4f4;
    --ink-soft: #c9c9c9;
    --ink-grey: #6e6e6e;
    --ink-tagline: #7a7a7a;
    --divider: #3a3a3a;
  }
  * { margin: 0; padding: 0; box-sizing: border-box; }
  html, body { width: 1200px; height: 844px; overflow: hidden; }
  body {
    background: var(--backdrop);
    font-family: "Open Sans", Arial, sans-serif;
    position: relative;
  }
  .card {
    position: absolute;
    top: 272px;
    width: 520px;
    height: 300px;
    background: linear-gradient(160deg, var(--card-edge), var(--card));
    border-radius: 4px;
    box-shadow: 0 18px 40px rgba(0,0,0,0.55);
  }
  .card--front { left: 50px; }
  .card--back { left: 630px; }

  .brand-name {
    font-weight: 600;
    letter-spacing: 1px;
    line-height: 1;
  }
  .card--front .brand-name {
    position: absolute;
    left: 40px;
    top: 178px;
    font-size: 40px;
    color: var(--ink-white);
  }
  .divider {
    position: absolute;
    left: 268px;
    top: 40px;
    width: 1px;
    height: 220px;
    background: var(--divider);
  }
  .contact {
    position: absolute;
    left: 290px;
    top: 44px;
    color: var(--ink-soft);
    font-size: 12.5px;
    line-height: 1.45;
  }
  .contact__name {
    color: var(--ink-white);
    font-size: 19px;
    font-weight: 600;
    line-height: 1.2;
  }
  .contact__role { font-size: 12px; margin-bottom: 14px; }
  .contact__lines { margin-bottom: 14px; }

  .card--back .brand-block {
    position: absolute;
    left: 50%;
    top: 110px;
    transform: translateX(-50%);
    display: flex;
    flex-direction: column;
    align-items: flex-end;
  }
  .card--back .brand-name {
    display: block;
    font-size: 56px;
    color: var(--ink-grey);
  }
  .tagline {
    display: block;
    margin-top: 6px;
    white-space: nowrap;
    font-family: "Cormorant Garamond", Georgia, serif;
    font-style: italic;
    font-size: 19px;
    color: var(--ink-tagline);
  }
</style>
</head>
<body>
  <section class="card card--front">
    <span class="brand-name">CORVANE</span>
    <span class="divider"></span>
    <div class="contact">
      <p class="contact__name">Luca Moretti</p>
      <p class="contact__role">Managing Director</p>
      <p class="contact__lines">T: 044-987 654 321<br>E: info@corvane.com<br>W: www.corvane.com</p>
      <p class="contact__offices">HQ Italy · Chicago · Moscow<br>Singapore · Agent in Brasil</p>
    </div>
  </section>

  <section class="card card--back">
    <div class="brand-block">
      <span class="brand-name">CORVANE</span>
      <span class="tagline">one team, one mission, global solution</span>
    </div>
  </section>
</body>
</html>
```